Hop Bright Meadow Business Website Branding

Looking for a wordpress template design with CSS and HTML encoding. Current website can be seen at hopbrightmeadow.example.

WE ARE CURRENTLY IN PROCESS GETTING A LOGO DESIGN... I HAVE INCLUDED THE TOP POTENTIAL DESIGNS FOR REFERENCE TO HELP UNDERSTAND WHAT STYLE WE ARE LOOKING FOR...
NOTE: THE “PEBBLE CREW” LOGO WAS A PREVIOUS COMPANY WE OWNED SO YOU CAN GE A FEEL FOR THE TYPE OF DESIGNS WE HAVE USED IN THE PAST.

My blog will focus on making a connection with wild Florida, it’s wildlife, plants and animals... with an eye toward Florida conservation, nature adventure trips, and education... Content, photos and other merchandise will also be offered for sale.
I’m looking for a site design that incorporates Florida nature and wildlife/plants, with a fun “Old Florida” retro-adventure feel.
When they see this site it should speak to the import of natural Florida and the critical nature of the ecosystem here... while being instantly recognizable and iconic... IE: when I think of florida I think of water, plants, warmth, sunsets etc...

https://join.chatroomhub.example/t/lumexstudio-kzt4821/shared_invite/zt-pqwrt83m-hRnLvXaKoPzsYcB1Uq7JdM

Target Market(s)

Nature, Education, Conservation, Photography

Industry/Entity Type

Photographer

Coding

Coded - Design and coding required

Requirements
Must have
• Need to have site wide template design which generally includes a landing page and a general page template for other pages... Must include html and css encoding...
Should not have
• Any animals included in the site should be Florida native... IE: no African animals etc... This will require some research to ensure that if animals are included that they are part of the Florida ecosystem.

```html
<!DOCTYPE html>
<html lang="en">
<head>
<meta charset="utf-8">
<title>Hop Bright Meadow</title>
<link rel="stylesheet" href="https://fonts.googleapis.com/css2?family=Amatic+SC:wght@400;700&family=Archivo+Narrow:ital,wght@1,400;1,500&family=Lato:wght@400;700&display=swap">
<style>
:root{
  --orange:#e05a1a;
  --orange-band:#e0883a;
  --leaf:#e6f1c7;
  --cream:#fbf3df;
  --mist:#eef0ef;
  --ink:#2b2b2b;
  --body:#4a4a4a;
  --muted:#8a8a7a;
  --white:#ffffff;
  --line:#d8dcc4;
}
*{margin:0;padding:0;box-sizing:border-box}
html,body{width:1200px;height:3071px;overflow:hidden}
body{position:relative;background:var(--white);font-family:"Lato",sans-serif;color:var(--ink)}
.abs{position:absolute}
.center{left:0;width:1200px;text-align:center}
.display{font-family:"Amatic SC",cursive;font-weight:700;line-height:1}

/* header */
.site-header{top:0;left:0;width:1200px;height:101px;background:var(--leaf);z-index:3}
.logo-dome{left:485px;top:20px;width:230px;height:135px;border-radius:0 0 115px 115px;background:var(--leaf);z-index:3}
.nav a{position:absolute;top:49px;font-size:14px;font-weight:700;color:#3a3a3a;text-decoration:none;letter-spacing:.2px;z-index:4}
.nav a.active{color:var(--orange)}
.nav a.active::after{content:"";position:absolute;left:-2px;right:-2px;top:22px;height:2px;background:var(--orange)}
.brand{display:flex;align-items:center;gap:8px;font-weight:700;color:var(--orange);z-index:5}
.brand .dot{width:16px;height:16px;border-radius:50%;background:var(--orange);flex:none}

/* hero */
.hero{top:101px;left:0;width:1200px;height:638px;background:linear-gradient(180deg,#2f5a6a 0%,#1d7f86 18%,#2b8a86 45%,#6e8b84 62%,#b5a98e 78%,#a99a7c 100%)}
.hero-title{top:290px;font-size:96px;color:var(--white);letter-spacing:6px;font-weight:400}
.hero-sub{top:394px;font-size:27px;color:var(--white);letter-spacing:1.5px}
.btn-solid{display:block;background:var(--orange);color:var(--white);font-size:19px;font-weight:400;text-align:center;line-height:46px;border-radius:2px;letter-spacing:.3px}

/* welcome */
.welcome{top:739px;left:0;width:1200px;height:310px;background:radial-gradient(ellipse at 50% 100%,#f7ead0 0%,var(--cream) 55%,#fdf8ec 100%)}
.section-title{font-size:60px;font-weight:400}
.welcome p{top:128px;left:180px;width:840px;font-size:16px;line-height:30px;color:#3b3b3b;text-align:center}

/* services */
.services-intro{top:1173px;left:160px;width:880px;text-align:center;font-size:15.5px;line-height:27px;color:#3b3b3b}
.card{top:1272px;width:233px;height:406px;border:1px solid #ececec;background:var(--white);box-shadow:0 0 3px rgba(0,0,0,.04)}
.card .photo{position:absolute;left:9px;top:9px;width:215px;height:155px}
.card h3{position:absolute;top:186px;left:0;width:100%;text-align:center;font-size:18px;font-weight:700;color:var(--orange)}
.card p{position:absolute;top:220px;left:20px;right:20px;text-align:center;font-size:12.5px;line-height:23px;color:#555}
.card .btn-line{position:absolute;top:332px;left:47px;width:139px;height:37px;border:1px solid var(--orange);color:var(--orange);font-size:14px;font-weight:700;text-align:center;line-height:35px;border-radius:2px}
.chev{stroke:#9a9a9a;fill:none;stroke-width:1.5}

/* about */
.about{top:1764px;left:0;width:1200px;height:441px;background:linear-gradient(180deg,#e48e3e 0%,var(--orange-band) 55%,#d97f32 100%)}
.about p{top:157px;left:120px;width:960px;text-align:center;color:#fbe3c8;font-size:18.5px;line-height:30px;letter-spacing:.3px}

/* testimonial */
.voices{top:2205px;left:0;width:1200px;height:495px;background:var(--mist)}
.avatar{left:526px;top:2321px;width:136px;height:136px;border-radius:50%;border:4px solid var(--white);box-shadow:0 0 0 1px #d7d7d7;background:linear-gradient(160deg,#3e8fae,#2bb2b8 55%,#a0673e)}
.quote{top:2474px;left:200px;width:800px;text-align:center;font-family:"Archivo Narrow",sans-serif;font-style:italic;font-size:19.5px;line-height:24px;color:#333}
.qmark{font-family:"Archivo Narrow",sans-serif;font-style:italic;font-size:64px;color:#b5b5b5;line-height:1}
.client-name{top:2539px;font-size:16px;font-weight:700;color:var(--orange)}
.client-role{top:2568px;font-size:11.5px;color:#333}
.dots span{position:absolute;top:2626px;width:7px;height:7px;border-radius:50%;background:#8a8a8a}
.dots span.on{background:var(--orange)}

/* footer */
.site-footer{top:2700px;left:0;width:1200px;height:371px;background:var(--leaf)}
.footer-about{top:2872px;left:112px;width:260px;text-align:center;font-size:13px;line-height:23.5px;color:var(--muted)}
.foot-col h4{position:absolute;top:2760px;font-size:20px;font-weight:400;color:var(--orange)}
.foot-col a{position:absolute;font-size:15.5px;color:#4a4a4a;text-decoration:none;display:flex;align-items:center;gap:9px}
.foot-col a .mark{width:11px;height:11px;background:var(--orange);border-radius:2px}
.foot-rule{top:2996px;left:111px;width:977px;height:1px;background:var(--line)}
.copyright{top:3022px;font-size:11.5px;color:#333}
.code{top:3022px;left:1128px;font-size:11.5px;color:#333}
</style>
</head>
<body>

<header class="site-header abs">
  <nav class="nav">
    <a class="active" style="left:116px">HOME</a>
    <a style="left:226px">ABOUT US</a>
    <a style="left:363px">SERVICES</a>
    <a style="left:773px">FEATURES</a>
    <a style="left:909px">BLOG</a>
    <a style="left:1015px">CONTACT</a>
  </nav>
</header>
<div class="logo-dome abs"></div>
<div class="brand abs" style="left:510px;top:54px;width:180px;justify-content:center;font-size:16px;letter-spacing:.4px"><span class="dot"></span>HOP BRIGHT MEADOW</div>

<section class="hero abs" role="img" aria-label="Photo of a sunny beach with turquoise surf and a row of gulls on the sand">
</section>
<svg class="abs" style="left:50px;top:397px" width="20" height="36" viewBox="0 0 20 36"><path d="M17 2 L3 18 L17 34" fill="none" stroke="#ffffff" stroke-opacity=".7" stroke-width="1.5"/></svg>
<svg class="abs" style="left:1126px;top:397px" width="20" height="36" viewBox="0 0 20 36"><path d="M3 2 L17 18 L3 34" fill="none" stroke="#ffffff" stroke-opacity=".7" stroke-width="1.5"/></svg>
<h1 class="hero-title abs center display">HOP BRIGHT MEADOW</h1>
<p class="hero-sub abs center">Exploring Florida’s Natural Wonders</p>
<a class="btn-solid abs" style="left:521px;top:454px;width:160px">LEARN MORE</a>

<section class="welcome abs">
  <h2 class="section-title display abs center" style="top:50px;color:var(--orange)">WELCOME TO HOP BRIGHT MEADOW</h2>
  <p class="abs">Come explore wild places and stunning scenery with me as I discover new and exciting eco-adventures and learn about the rare and unique wildlife and environments that make Florida so precious and extraordinary. I hope you can vicariously enjoy the wild and untamed beauty of Florida through my eyes, and learn some amazing things about nature on our explorations.</p>
</section>

<section class="services">
  <h2 class="section-title display abs center" style="top:1101px;color:var(--ink)">HOP BRIGHT SERVICES</h2>
  <p class="services-intro abs">Sed do eiusmod tempor incididunt ut labore et dolore magna aliqua. Ut enim ad minim veniam, quis nostrud exercitation ullamco laboris nisi ut aliquip ex ea commodo consequat.</p>

  <svg class="abs" style="left:42px;top:1406px" width="30" height="60" viewBox="0 0 30 60"><path class="chev" d="M28 2 L2 30 L28 58"/></svg>
  <svg class="abs" style="left:1124px;top:1406px" width="30" height="60" viewBox="0 0 30 60"><path class="chev" d="M2 2 L28 30 L2 58"/></svg>

  <article class="card abs" style="left:111px">
    <div class="photo" role="img" aria-label="Close-up photo of a red and yellow lily flower" style="background:linear-gradient(135deg,#e8455a,#f07a5c 45%,#5e9a3a)"></div>
    <h3>EIUSMOD TEMPOR</h3>
    <p>Temporibus autem quibusdam et aut officiis debitis aut rerum necessitatibus saepe eveniet ut et voluptates repudiandae.</p>
    <a class="btn-line">Learn More</a>
  </article>
  <article class="card abs" style="left:360px">
    <div class="photo" role="img" aria-label="Photo of a pale buckeye butterfly resting on dry leaves" style="background:linear-gradient(135deg,#4a3d2c,#c9b69a 50%,#3b3024)"></div>
    <h3>SEQUI NESCIUNT</h3>
    <p>Temporibus autem quibusdam et aut officiis debitis aut rerum necessitatibus saepe eveniet ut et voluptates repudiandae.</p>
    <a class="btn-line">Learn More</a>
  </article>
  <article class="card abs" style="left:608px">
    <div class="photo" role="img" aria-label="Photo of purple blazing star wildflowers among green foliage" style="background:linear-gradient(135deg,#3f7a3a,#a46ac8 50%,#4c8a3e)"></div>
    <h3>SAPIENTE DELECTUS</h3>
    <p>Temporibus autem quibusdam et aut officiis debitis aut rerum necessitatibus saepe eveniet ut et voluptates repudiandae.</p>
    <a class="btn-line">Learn More</a>
  </article>
  <article class="card abs" style="left:857px">
    <div class="photo" role="img" aria-label="Photo of a marsh river at sunset under a pink sky" style="background:linear-gradient(180deg,#c99aa8,#d8a4a0 35%,#4a5a3a 60%,#7d7a72)"></div>
    <h3>VOLUPTATIBUS MAIO</h3>
    <p>Temporibus autem quibusdam et aut officiis debitis aut rerum necessitatibus saepe eveniet ut et voluptates repudiandae.</p>
    <a class="btn-line">Learn More</a>
  </article>
</section>

<section class="about abs" role="img" aria-label="Orange-tinted photo of birds splashing on water">
  <h2 class="section-title display abs center" style="top:86px;color:var(--white)">ABOUT US</h2>
  <p class="abs">Nemo enim ipsam voluptatem quia voluptas sit aspernatur aut odit aut fugit, sed quia consequuntur magni dolores eos qui ratione voluptatem sequi nesciunt. Neque porro quisquam est, qui dolorem ipsum quia dolor sit amet, consectetur, adipisci velit, sed quia non numquam eius modi tempora incidunt ut labore</p>
  <a class="btn-solid abs" style="left:521px;top:277px;width:160px">LEARN MORE</a>
</section>

<section class="voices abs">
  <h2 class="section-title display abs center" style="top:44px;color:var(--ink)">WHAT OUR CLIENT SAYING</h2>
</section>
<div class="avatar abs" role="img" aria-label="Portrait photo of the client by the sea"></div>
<span class="qmark abs" style="left:182px;top:2456px">“</span>
<span class="qmark abs" style="left:988px;top:2498px">”</span>
<p class="quote abs">Nature has been for me, as long as I remember, a source of solace, inspiration, adventure, and delight; a home, a teacher, a companion.</p>
<p class="client-name abs center">MARISOL PENDLETON</p>
<p class="client-role abs center">(ACCUSANTIUM DOLOREMQUE LAUDANTIUM, TOTAM)</p>
<div class="dots">
  <span class="on" style="left:571px"></span>
  <span style="left:588px"></span>
  <span style="left:605px"></span>
  <span style="left:622px"></span>
</div>

<footer class="site-footer abs"></footer>
<div class="brand abs" style="left:132px;top:2820px;width:220px;justify-content:center;font-size:17px;letter-spacing:.4px"><span class="dot"></span>HOP BRIGHT MEADOW</div>
<p class="footer-about abs">Temporibus autem quibusdam et aut officiis debitis aut rerum necessitatibus saepe eveniet ut et voluptates repudiandae sint et molestiae</p>

<div class="foot-col">
  <h4 style="left:505px">Links</h4>
  <a style="left:506px;top:2808px">Home</a>
  <a style="left:506px;top:2840px">About</a>
  <a style="left:506px;top:2872px">Services</a>
  <a style="left:506px;top:2903px">Blog</a>
  <a style="left:506px;top:2935px">Contact</a>
</div>
<div class="foot-col">
  <h4 style="left:753px">Resources</h4>
  <a style="left:755px;top:2808px">Blog</a>
  <a style="left:755px;top:2840px">Delivery</a>
  <a style="left:755px;top:2872px">Help</a>
  <a style="left:755px;top:2903px">Terms &amp; conditions</a>
  <a style="left:755px;top:2935px">Privacy policy</a>
</div>
<div class="foot-col">
  <h4 style="left:975px">Get In Touch</h4>
  <a style="left:976px;top:2812px"><span class="mark"></span>Friendbook</a>
  <a style="left:976px;top:2844px"><span class="mark"></span>Chirpline</a>
  <a style="left:976px;top:2876px"><span class="mark"></span>Snapframe</a>
  <a style="left:976px;top:2907px"><span class="mark"></span>Clipstream</a>
</div>

<div class="foot-rule abs"></div>
<p class="copyright abs center">Copyrights © 2020 HOP BRIGHT MEADOW.&nbsp; All Rights Reserved.</p>
<p class="code abs">C16</p>

</body>
</html>
```